Doctor to Patient Management Website

I need a design for a health management website that connects doctors to patients. The website will consist of: A main page mainly describing our goal, services, and initiatives towards (Who we are AKA "About Us", Our services, Contact Us, Quick Links for health tips, Language selection, Find a doctor, search bar, Member Login Section, small glossary section below with links to all entities mentioned prior, Help section (Helpful tips and tutorials, Used to request help from admin, customer service, to resolve issues or get assistance). A profile page with two types:1) Doctor Profile: Doctor Personal info (First, Last, Middle Name, Title), Clinic, Hospital Info, Department, Credentials, Years of Experience, Patients rating, #Patients seen during the current week, #Patients seen in total, Picture, Link to email doctor, Link to print doctor's profile). Tabs for "About Me", "Contact Info", "Ratings & Comments", "Documents" (To be downloaded and uploaded by patient), "Patients (List of Patients alphabetical order by name)", "Calendar" (to see doctor's availability for booking) underneath all links. 2) Patient profile: About me, Personal Info, Height, Weight, Blood Type, Age, DOB, Name, etc..., Message and email link.Picture of patient with menu made of "Personal Data", "Biometrics", "Allergies", "Illnesses", "Medications", "Medical Procedures", "Doctors" treating the patient, "Documents" (To be downloaded and uploaded by patient). Underneath all, other patients he or she is related to (For example: family member, so patient can't connect to other patients who are family members)3) Login section: New Users will have option to register using:First Name (Required), Last Name, Middle (not required), Address (Not required), City (Required), Country (Required), Email (Not required), Phone Number (Required), Choose UserName, Password, Account Type (Doctor or Patient). Once registered, they will log in using UserName, Password, and Account_Type.Curent Users will log in using UserName, Password, and Account_Type and option to retrieve username or password.Pages to include (Login Page - Registration Page - Retrieve Username and Reset Password Page)Please see link below:https://plumcrate-adwerks.net/importance-claiming-vantorix-quibble-zarn/Pictures are attached to this project as an inspirationFYI: Dummy text can be used to fill in the business, services, and descriptive information. Feel free to include your own ideas in the layout, design, categories, patterns, and more to and showcase your talent. Design and pictures provided are available as source of ideas.

Target Market(s)

Age: 21+ / Family Oriented / Medical Sector / Metropolitan Area / Educated and non Educated Users

Industry/Entity Type

Health Care

Number of Pages Required

5+ page

Font styles to use
Sans Serif

Colors

Designer to choose colors to be used in the design.

Requirements
Must have
• Thin layer design
• Simple font - No serif
• Clean menu with light but solid colors (No Gradient effect)
Nice to have
• Different color themes (2 or 3) can be combined
• Sample pictures for illustration (either as an ad or to go with the flow of your design)
• Dashboard Feel (Suggested but not required)
Should not have
• Artistic fonts - with Serif
• Dark color themes

```html
<!DOCTYPE html>
<html lang="en">
<head>
<meta charset="utf-8">
<title>Velmora – Be Healthy and Productive</title>
<link href="https://fonts.googleapis.com/css2?family=Arimo:wght@400;700&family=Open+Sans:wght@400;600;700&family=Muli:wght@400;600;700;800&display=swap" rel="stylesheet">
<style>
:root{
  --teal:#2fa58f;
  --ink:#2f2f2f;
  --body:#666;
  --line:#e3e3e3;
  --mint:#eef7f5;
  --panel:#3b3b3b;
  --footer:#243331;
  --white:#fff;
}
*{box-sizing:border-box;margin:0;padding:0}
html,body{width:1200px;height:3237px;overflow:hidden;background:var(--white)}
body{font-family:"Arimo",Arial,sans-serif;color:var(--body);position:relative}
.abs{position:absolute}
h1,h2,h3,.brand{font-family:"Muli","Open Sans",sans-serif}
.brand{font-weight:700;letter-spacing:2px;color:var(--ink);font-size:30px}

/* header */
.header{top:0;left:0;width:1200px;height:112px;background:var(--white)}
.utility{top:22px;font-family:"Open Sans",sans-serif;font-size:13px;color:#444;display:flex;align-items:center;gap:6px}
.util-sep{top:20px;width:1px;height:22px;background:#333}
.social{top:20px;width:22px;height:22px;border:1px solid #bbb;border-radius:50%}
.nav{top:72px;font-family:"Open Sans",sans-serif;font-size:14px;color:#333;font-weight:600}
.nav.active{border-bottom:2px solid var(--teal);padding-bottom:4px}
.cta{top:65px;left:910px;width:115px;height:32px;background:var(--teal);color:#fff;font-family:"Open Sans",sans-serif;font-size:14px;font-weight:700;display:flex;align-items:center;justify-content:center}

/* hero */
.hero{top:112px;left:0;width:1200px;height:460px;background:linear-gradient(90deg,#8c8682 0%,#cfc8c0 35%,#e6e1da 60%,#b9aa9b 100%)}
.hero-kicker{top:258px;left:172px;color:#fff;font-family:"Open Sans",sans-serif;font-weight:700;font-size:18px}
.hero-title{top:288px;left:172px;color:#fff;font-weight:800;font-size:40px;line-height:48px}
.search{top:402px;left:170px;width:400px;height:56px;background:#fff;border-radius:28px;box-shadow:0 4px 14px rgba(0,0,0,.15)}
.search span{position:absolute;left:26px;top:18px;font-size:15px;color:#555}
.search b{position:absolute;right:4px;top:4px;width:172px;height:48px;border-radius:24px;background:var(--teal);color:#fff;font-size:16px;display:flex;align-items:center;justify-content:center}
.counter{top:518px;left:1073px;color:#fff;font-size:28px;font-weight:700}
.counter small{font-size:15px;font-weight:400}

/* about */
.about-photo{top:600px;left:105px;width:470px;height:497px;background:linear-gradient(180deg,#f4f1ee,#e2e6ee 60%,#c9d3e4)}
h2.title{font-weight:600;color:var(--ink);font-size:28px}
.para{font-size:12.5px;line-height:24px;color:var(--body)}
.about-copy{left:637px;top:660px;width:395px;display:flex;flex-direction:column}
.about-copy .para{margin:14px 0 10px 3px}
.check{display:flex;gap:10px;font-size:12.5px;line-height:22px;margin-bottom:12px}
.check svg{flex:none;margin-top:1px}
.divider-band{top:1090px;left:0;width:1200px;height:12px;background:linear-gradient(#fff,#f1f4f3)}

/* services */
.card{top:1288px;width:207px;height:292px;border:1px solid var(--line);background:#fff}
.card .ph{height:162px;background:linear-gradient(135deg,#c9c2b8,#8a94a3)}
.card h3{font-family:"Arimo",Arial,sans-serif;font-size:14px;color:var(--ink);font-weight:700;margin:22px 0 6px 12px}
.card p{font-size:12px;line-height:22px;margin:0 12px}
.btn-pill{background:var(--teal);color:#fff;font-weight:700;font-size:14px;border-radius:26px;display:flex;align-items:center;justify-content:center}

/* contact */
.contact-copy{left:173px;top:1824px;width:515px;display:flex;flex-direction:column}
.contact-copy .para{margin-bottom:10px}
.contact-box{top:1828px;left:747px;width:278px;height:307px;background:var(--panel)}
.field{position:absolute;left:15px;width:248px;height:38px;border:1px solid #bbb;border-radius:4px;color:#fff;font-size:13px;padding:10px 12px}

/* help */
.help{top:2218px;left:0;width:1200px;height:302px;background:var(--mint)}
.ghost{border:2px solid var(--teal);color:var(--teal);border-radius:20px;font-weight:700;font-size:13px;display:flex;align-items:center;justify-content:center;background:#fff}
.tips li{list-style:none;font-size:13.5px;color:#444;height:35px;display:flex;gap:14px;align-items:center}
.tut{width:218px;height:98px;background:linear-gradient(135deg,#cfd9e4,#8aa2b8)}

/* footer */
.footer{top:2940px;left:0;width:1200px;height:297px;background:var(--footer);color:#fff}
.footer h4{font-size:12px;font-weight:700;letter-spacing:.5px}
.footer ul{list-style:none;font-size:11px;line-height:26px;margin-top:10px}
</style>
</head>
<body>

<header class="abs header">
  <div class="abs brand" style="left:172px;top:36px">VELMORA</div>
  <div class="abs utility" style="left:590px">English
    <svg width="9" height="6" viewBox="0 0 9 6"><path d="M1 1l3.5 3.5L8 1" stroke="#444" fill="none" stroke-width="1.4"/></svg></div>
  <div class="abs utility" style="left:668px">
    <svg width="18" height="18" viewBox="0 0 18 18"><circle cx="9" cy="9" r="8" fill="none" stroke="#444"/><path d="M6 5l2 2-1 1c.5 1.2 1.5 2.2 2.7 2.7l1-1 2 2-1.2 1.2C8.5 12.5 5.5 9.5 5 7.2z" fill="#444"/></svg>
    +1 - 555-010-0199</div>
  <div class="abs util-sep" style="left:826px"></div>
  <div class="abs utility" style="left:846px;font-size:11px">
    <svg width="14" height="14" viewBox="0 0 14 14"><circle cx="7" cy="4.5" r="3" fill="none" stroke="#444"/><path d="M1.5 13c0-3 2.5-4.5 5.5-4.5s5.5 1.5 5.5 4.5" fill="none" stroke="#444"/></svg>
    Member Login</div>
  <div class="abs util-sep" style="left:960px"></div>
  <div class="abs social" style="left:975px"></div>
  <div class="abs social" style="left:1003px"></div>
  <div class="abs nav active" style="left:518px">Home</div>
  <div class="abs nav" style="left:588px">Our services</div>
  <div class="abs nav" style="left:700px">Health Tips</div>
  <div class="abs nav" style="left:805px">Contact Us</div>
  <div class="abs cta">Find a doctor</div>
</header>

<section class="abs hero" role="img" aria-label="Photo of a doctor consulting a patient at a desk in a bright clinic office"></section>
<div class="abs hero-kicker">Velmora</div>
<h1 class="abs hero-title">BE HEALTHY<br>AND PRODUCTIVE</h1>
<div class="abs search"><span>Find Doctor</span><b>SEARCH NOW</b></div>
<div class="abs counter">01 <small>/ 04</small>
  <svg width="12" height="16" viewBox="0 0 12 16" style="margin-left:6px"><path d="M3 2l6 6-6 6" stroke="#fff" stroke-width="2" fill="none"/></svg></div>

<div class="abs about-photo" role="img" aria-label="Photo of a smiling female doctor holding a clipboard and presenting with an open hand"></div>
<div class="abs about-copy">
  <h2 class="title">ABOUT US</h2>
  <p class="para">Sed ut perspiciatis unde omnis iste natus error sit voluptatem accusant ium dol oremque laudantium, totam rem aperiam, eaque ipsa quae ab illo inventore veritatis et quasi architecto beatae vitae dicta sunt explicabo enim ipsam voluptatem voluptas aspernatur autodit autugit.</p>
  <div class="check"><svg width="20" height="20" viewBox="0 0 20 20"><circle cx="10" cy="10" r="9" fill="none" stroke="var(--teal)" stroke-width="2"/><path d="M5.5 10l3 3 6-6" stroke="var(--teal)" stroke-width="2" fill="none"/></svg><span>At vero eos et accusamus et iusto odio dignissimos ducimus qui blanit ditiis praesen tium voluptatum deleniti dolore.</span></div>
  <div class="check"><svg width="20" height="20" viewBox="0 0 20 20"><circle cx="10" cy="10" r="9" fill="none" stroke="var(--teal)" stroke-width="2"/><path d="M5.5 10l3 3 6-6" stroke="var(--teal)" stroke-width="2" fill="none"/></svg><span>Cero eos et accusamus et iusto odio dignissimos.</span></div>
  <div class="check"><svg width="20" height="20" viewBox="0 0 20 20"><circle cx="10" cy="10" r="9" fill="none" stroke="var(--teal)" stroke-width="2"/><path d="M5.5 10l3 3 6-6" stroke="var(--teal)" stroke-width="2" fill="none"/></svg><span>Setro eos et accusamus et iusto odio dignissimos ducimus qui blanditiis praesen tium voluptatum deleniites.</span></div>
  <div class="check"><svg width="20" height="20" viewBox="0 0 20 20"><circle cx="10" cy="10" r="9" fill="none" stroke="var(--teal)" stroke-width="2"/><path d="M5.5 10l3 3 6-6" stroke="var(--teal)" stroke-width="2" fill="none"/></svg><span>Vero eos et accusamus et iusto odio dignissimose utas.</span></div>
</div>
<div class="abs divider-band"></div>

<h2 class="abs title" style="left:0;width:1200px;text-align:center;top:1170px">OUR SERVICES</h2>
<p class="abs para" style="left:280px;width:640px;text-align:center;top:1215px;font-size:12px">Lorem ipsum dolor sit amet, consectetur adipiscing elit, sed do eiusmod tempor incidi dunt ut labore et dolore magna aliqua. Ut enimainim veniam, quis nostrud exercitea bonual lamco aliquip commodo consequat.</p>
<div class="abs card" style="left:177px"><div class="ph" role="img" aria-label="Photo of a therapist assisting a patient with rehabilitation exercise"></div><h3>Occupational Health</h3><p>Sed doas eiusmod tempor incidi dunt uta laboreat dolores magna aliquat enimad mainim.</p></div>
<div class="abs card" style="left:390px"><div class="ph" role="img" aria-label="Photo of a child at an eye chart during a primary care check"></div><h3>Primary Care</h3><p>Sed doas eiusmod tempor incidi dunt uta laboreat dolores magna aliquat enimad mainim.</p></div>
<div class="abs card" style="left:604px"><div class="ph" role="img" aria-label="Photo of a family visiting a doctor"></div><h3>Wellbeing</h3><p>Sed doas eiusmod tempor incidi dunt uta laboreat dolores magna aliquat enimad mainim.</p></div>
<div class="abs card" style="left:817px"><div class="ph" role="img" aria-label="Photo of hands reviewing health reports on a table"></div><h3>Health Surveillance</h3><p>Sed doas eiusmod tempor incidi dunt uta laboreat dolores magna aliquat enimad mainim.</p></div>
<div class="abs btn-pill" style="left:493px;top:1612px;width:214px;height:50px">EXPLORE ALL SERVICES</div>
<div class="abs divider-band" style="top:1718px"></div>

<div class="abs contact-copy">
  <div style="color:var(--teal);font-weight:700;font-size:13px">LOREM IPSUM</div>
  <h2 style="font-size:34px;font-weight:800;color:var(--ink);margin:6px 0 16px">GET IN TOUCH WITH US</h2>
  <p class="para">Sed ut perspiciatis unde omnis iste natus error sit voluptatem accusantium doloremque laudant ium, totam rem aperiam, eaque ipsa quae ab illo inventore veritatis et quasi architecto beatae vitae dicta sunt explicabo. Nemo enim ipsam voluptatem quia voluptas sit aspernatur aut odit aut fugit, sed quia consequuntur magni dolores ipsum quia dolo .</p>
  <p class="para">Pespiciatis unde omnis iste natus error sit voluptatem accusantium doloremque laudant ium, totam rem aperiam, eaque ipsaed ut perspiciatis unde omnis iste natus error sit voluptatem acc usantium doloremque laudantium, totam rem aperiam, eaque ipsa quae ab illo inventore veritatis et quasi architecto beatae vitae dicta sunt explicabo.</p>
</div>
<div class="abs contact-box">
  <div class="abs" style="left:16px;top:20px;color:#fff;font-weight:700;font-size:14px">CONTACT US</div>
  <div class="field" style="top:54px">Full Name</div>
  <div class="field" style="top:100px">Email Address</div>
  <div class="field" style="top:146px;height:78px">Enter Message</div>
  <div class="abs btn-pill" style="left:15px;top:244px;width:248px;height:40px;border:2px solid #fff;font-size:15px">SEND MESSAGE</div>
</div>

<section class="abs help"></section>
<h2 class="abs title" style="left:0;width:1200px;text-align:center;top:2276px">HELP</h2>
<p class="abs para" style="left:280px;width:640px;text-align:center;top:2328px;font-size:12px">Quae ab illo inventore veritatis et quasi architecto beatae vitae dicta sunt explicabo. Nemo enim ipsam voluptatem quia voluptas sit aspernatur aut odit aut fugit, sed quia consequuntur magni dolores eos qui ratione voluptatem sequi inventore veritatis nesciunt. Neque porro quisquam est, qui dolorem ipsum.</p>
<div class="abs ghost" style="left:540px;top:2428px;width:120px;height:32px">VIEW MORE</div>

<h2 class="abs" style="left:173px;top:2600px;font-size:32px;font-weight:600;color:var(--ink)">HELP TIPS</h2>
<ul class="abs tips" style="left:173px;top:2643px">
  <li><svg width="9" height="10" viewBox="0 0 9 10"><path d="M1 1l4 4-4 4M4 1l4 4-4 4" stroke="#555" fill="none"/></svg>Sed quia consequuntur magni dolores eos qui ratione</li>
  <li><svg width="9" height="10" viewBox="0 0 9 10"><path d="M1 1l4 4-4 4M4 1l4 4-4 4" stroke="#555" fill="none"/></svg>Dolore magnam aliquam quaerat voluptatem.</li>
  <li><svg width="9" height="10" viewBox="0 0 9 10"><path d="M1 1l4 4-4 4M4 1l4 4-4 4" stroke="#555" fill="none"/></svg>Ut enimad minima veniam, quis nostrum exercitat</li>
  <li><svg width="9" height="10" viewBox="0 0 9 10"><path d="M1 1l4 4-4 4M4 1l4 4-4 4" stroke="#555" fill="none"/></svg>Voluptate velit esse cillum dolore eu fugiat nulla pariatur.</li>
  <li><svg width="9" height="10" viewBox="0 0 9 10"><path d="M1 1l4 4-4 4M4 1l4 4-4 4" stroke="#555" fill="none"/></svg>Quis autem vel eum iure reprehenderit quinea volu</li>
  <li><svg width="9" height="10" viewBox="0 0 9 10"><path d="M1 1l4 4-4 4M4 1l4 4-4 4" stroke="#555" fill="none"/></svg>Lorem ipsum dolor sit amet, consectetur adipiscing e</li>
</ul>
<h3 class="abs" style="left:575px;top:2603px;color:var(--teal);font-size:19px;font-weight:700">Our Tutorials</h3>
<div class="abs tut" style="left:575px;top:2642px" role="img" aria-label="Tutorial video still of a medical examination"></div>
<div class="abs tut" style="left:807px;top:2642px;background:linear-gradient(135deg,#e3e8ec,#9fb0bd)" role="img" aria-label="Tutorial video still of a stethoscope and tablet"></div>
<div class="abs tut" style="left:575px;top:2757px;background:linear-gradient(135deg,#c4d0de,#5f7891)" role="img" aria-label="Tutorial video still of a medical team"></div>
<div class="abs tut" style="left:807px;top:2757px;background:linear-gradient(135deg,#dfe3e6,#8c98a4)" role="img" aria-label="Tutorial video still of doctors in a meeting"></div>

<footer class="abs footer">
  <div class="abs brand" style="left:173px;top:57px;color:#fff;font-size:26px;font-weight:400">VELMORA</div>
  <p class="abs" style="left:173px;top:105px;width:290px;font-size:11px;line-height:22px">Sed ut perspiciatis unde omnis iste natus error sit volupi daterns accusantium doloremque laudantium, totam rem aperiam, eaque ipsa quae ab illo inventore veritatis etas quasi architecto beatae vitae dicta sunt explicabo ratione voluptatem dolorem vitsseas.</p>
  <div class="abs" style="left:593px;top:58px"><h4>QUICK LINKS</h4><ul><li>ABOUT US</li><li>OUR SERVICES</li><li>HEALTH TIPS</li><li>CONTACT US</li></ul></div>
  <div class="abs" style="left:775px;top:58px"><h4>GLOSSARY</h4><ul><li>HELP</li><li>CUSTOMERS</li><li>REFERRALS</li></ul></div>
  <div class="abs" style="left:938px;top:58px"><h4>LEGAL</h4><ul><li>TERMS OF USE</li><li>PRIVACY POLICY</li></ul></div>
  <div class="abs" style="left:173px;top:238px;width:855px;height:1px;background:rgba(255,255,255,.35)"></div>
  <div class="abs" style="left:173px;top:262px;font-size:13px;display:flex;gap:14px;align-items:center">
    <svg width="13" height="13" viewBox="0 0 18 18"><path d="M3 1l4 4-2 2c1 2.5 3.5 5 6 6l2-2 4 4-2.5 2.5C8 16.5 1.5 10 .5 3.5z" fill="#fff"/></svg>+1- 555-010-0199</div>
  <div class="abs" style="left:698px;top:263px;display:flex;gap:16px">
    <span style="width:12px;height:12px;border:1px solid #fff;border-radius:50%"></span>
    <span style="width:12px;height:12px;border:1px solid #fff;border-radius:50%"></span>
    <span style="width:12px;height:12px;border:1px solid #fff;border-radius:50%"></span>
    <span style="width:12px;height:12px;border:1px solid #fff;border-radius:50%"></span>
  </div>
  <div class="abs" style="left:838px;top:263px;font-size:11px">Copyright © 2019. All Rights Reserved</div>
</footer>

</body>
</html>
```